Moravel Aesthetic Doctor

I require an elegant, luxurious looking business card for my aesthetic business. I am a doctor and that will set me aside from competitors. I am planning to provide home and spa based treatments to clients with high expectations. I have attached my logo.

```html
<!DOCTYPE html>
<html lang="en">
<head>
<meta charset="utf-8">
<title>Moravel Aesthetic Doctor – Business Card</title>
<link href="https://fonts.googleapis.com/css2?family=Roboto:wght@300;400;500&display=swap" rel="stylesheet">
<style>
  :root {
    --backdrop: #3b3b3d;
    --card: #1f2023;
    --card-edge: #2a2b2f;
    --silver: #9a9ca0;
    --name-grey: #c3c5c8;
    --accent: #4fb0e8;
    --text-light: #e4e6e8;
  }
  * { margin: 0; padding: 0; box-sizing: border-box; }
  html, body { width: 799px; height: 1200px; overflow: hidden; }
  body {
    background: var(--backdrop);
    font-family: "Roboto", sans-serif;
    position: relative;
  }
  .card {
    position: absolute;
    left: 70px;
    width: 659px;
    height: 377px;
    background: var(--card);
    border-radius: 6px;
    box-shadow: 0 14px 30px rgba(0,0,0,0.45);
    overflow: hidden;
  }
  .card--front { top: 118px; }
  .card--back { top: 705px; }

  .brand {
    position: absolute;
    left: 50%; top: 50%;
    transform: translate(-50%, -50%);
    display: flex; align-items: center; gap: 14px;
  }
  .brand__dot {
    width: 18px; height: 18px; border-radius: 50%;
    border: 2px solid var(--silver);
  }
  .brand__name {
    font-weight: 300;
    font-size: 40px;
    letter-spacing: 3px;
    color: var(--silver);
  }

  .holder { position: absolute; left: 40px; top: 40px; }
  .holder__name {
    font-weight: 300; font-size: 27px; color: var(--name-grey);
  }
  .holder__post {
    font-size: 13px; font-style: italic; color: var(--accent); margin-top: 6px;
  }
  .holder__diploma {
    font-size: 16px; color: var(--accent); margin-top: 3px;
  }

  .contacts {
    position: absolute; left: 40px; top: 195px;
    list-style: none;
    font-size: 15px; color: var(--text-light);
  }
  .contacts li { display: flex; align-items: center; gap: 12px; height: 24px; }
  .contacts svg { width: 13px; height: 13px; fill: var(--text-light); }
  .contacts .follow { gap: 8px; }
  .contacts .follow__handle { color: var(--accent); }

  .tagline {
    position: absolute;
    left: 245px; right: 0; bottom: 40px;
    height: 40px;
    background: var(--accent);
    border-radius: 20px 0 0 20px;
    display: flex; align-items: center; justify-content: center;
    font-size: 19px; color: #ffffff;
  }
</style>
</head>
<body>
  <section class="card card--front" aria-label="Card front">
    <div class="brand">
      <span class="brand__dot"></span>
      <span class="brand__name">Moravel</span>
    </div>
  </section>

  <section class="card card--back" aria-label="Card back">
    <div class="holder">
      <p class="holder__name">Dr Elsa Marren</p>
      <p class="holder__post">MRCPCH MD</p>
      <p class="holder__diploma">Australasian Diploma of Aesthetic Medicine</p>
    </div>

    <ul class="contacts">
      <li>
        <svg viewBox="0 0 24 24"><path d="M6.6 10.8a15 15 0 0 0 6.6 6.6l2.2-2.2c.3-.3.7-.4 1-.2 1.1.4 2.3.6 3.6.6.6 0 1 .4 1 1V20c0 .6-.4 1-1 1A17 17 0 0 1 3 4c0-.6.4-1 1-1h3.5c.6 0 1 .4 1 1 0 1.3.2 2.5.6 3.6.1.3 0 .7-.2 1z"/></svg>
        <span>0800 555 014</span>
      </li>
      <li>
        <svg viewBox="0 0 24 24"><path d="M2 5h20v14H2z M3.5 6.5 12 13l8.5-6.5" fill="none" stroke="#e4e6e8" stroke-width="2"/></svg>
        <span>elsa@moravel.co.nz</span>
      </li>
      <li>
        <svg viewBox="0 0 24 24"><g fill="none" stroke="#e4e6e8" stroke-width="2"><circle cx="12" cy="12" r="9"/><ellipse cx="12" cy="12" rx="4" ry="9"/><path d="M3 12h18"/></g></svg>
        <span>www.moravel.co.nz</span>
      </li>
      <li class="follow">
        <span>Follow us on:</span>
        <span class="follow__handle">@moravelclinic</span>
      </li>
    </ul>

    <div class="tagline">Home &amp; Spa Based Treatments</div>
  </section>
</body>
</html>
```